real estate managers brochure A5

Real estate services brochure (owners corporation management)

Content has been uploaded in MS word documents and we reserve the right to refine the text in one revision.

Visit out site http://www.marrowfen.com.au/body-corporate-managers/ and review the pages in the 'owners corporation' menu in our website - the brochure is for these services we provide.

We want to showcase a variety of 'trophy' buildings/unit/apartment/factory developments that we manage - I've uploaded these 'case studies' and high res images for each.

Some General services photos to be provided by you.

The brochure is given out to potential owners who we wish to be clients.

We are going to print a few dozen of these in hard copy so will need artwork in nigh resolution pdf format and a web resolution version for emailing potential clients.

Target Market(s)

Unit owners, apartment owners and commercial factory owners

Industry/Entity Type

Property Management

Font styles to use
Serif
Sans Serif

Requirements
Must have
• A modern design that looks like it could be just as home on a website or facebook post
• Have a flair of retro design and/or vintage graphics
• 3 full pages of example properties we manage property. see example properties in the case studies. I have uploaded high res images for the full page images and some brief text for these pages
Should not have
• Must not look like a typical real estate agents brochure (smiling agents, happy home owners)
• Images of people who do not look australian (ie afro american, asian) as this is not our target market. We typically have anglo australian or eruopean looking clients
• We are a young company who pride ourselves on. Efficient services and high tech management systems for the properties we manage

```html
<!DOCTYPE html>
<html lang="en">
<head>
<meta charset="utf-8">
<title>Accreditations &amp; affiliations</title>
<link href="https://fonts.googleapis.com/css2?family=Raleway:wght@300&family=Open+Sans:wght@400;600;700&display=swap" rel="stylesheet">
<style>
  :root {
    --brand-blue: #2b4b9c;
    --heading-blue: #2c4f9e;
    --brand-green: #3db54a;
    --body-grey: #6b6b6b;
    --paper: #ffffff;
  }
  * { box-sizing: border-box; margin: 0; padding: 0; }
  html, body { width: 854px; height: 1200px; overflow: hidden; background: var(--paper); }
  .page {
    position: relative; width: 854px; height: 1200px; overflow: hidden;
    font-family: "Open Sans", Arial, sans-serif; background: var(--paper);
  }
  .page-title {
    position: absolute; left: 36px; top: 14px;
    font-family: "Raleway", Helvetica, sans-serif; font-weight: 300;
    font-size: 45px; color: var(--heading-blue); letter-spacing: 0.3px;
  }
  .title-rule { position: absolute; left: 0; top: 82px; }
  .affiliations {
    position: absolute; left: 24px; top: 118px; width: 802px;
    border-collapse: collapse; color: #fff; font-size: 15px;
  }
  .affiliations td {
    border: 2px solid var(--paper); padding: 0 14px; vertical-align: middle;
    height: 43px;
  }
  .affiliations .label {
    background: var(--brand-blue); width: 400px; font-weight: 700;
  }
  .affiliations .label.top { vertical-align: top; padding-top: 11px; }
  .affiliations .value { background: var(--brand-green); font-weight: 700; }
  .affiliations .value.tall { height: 69px; line-height: 1.35; }
  .value .sep { font-weight: 400; margin: 0 6px; }
  .value .url { font-weight: 400; }
  .value .url-line { display: block; font-weight: 400; }
  .indemnity { position: absolute; left: 38px; top: 532px; width: 790px; }
  .indemnity h2 {
    font-size: 24px; font-weight: 700; color: var(--heading-blue); line-height: 1.2;
  }
  .indemnity p {
    margin-top: 4px; font-size: 17px; line-height: 25px; color: var(--body-grey);
  }
  .garden-photo {
    position: absolute; left: 0; top: 667px; width: 854px; height: 533px;
    background: linear-gradient(180deg, #cfe3f4 0%, #e6eff6 22%, #8fa86a 45%, #6f8a3f 62%, #c9a86a 82%, #9a8a70 100%);
  }
</style>
</head>
<body>
<main class="page">
  <h1 class="page-title">Accreditations &amp; affiliations</h1>
  <svg class="title-rule" width="650" height="14" viewBox="0 0 650 14" aria-hidden="true">
    <line x1="0" y1="7" x2="632" y2="7" stroke="#2c4f9e" stroke-width="2"/>
    <circle cx="636" cy="7" r="6.5" fill="#2c4f9e"/>
  </svg>

  <table class="affiliations">
    <tr><td class="label">Licenced Owners Corporation Managers</td><td class="value">000482</td></tr>
    <tr><td class="label">Licenced Estate Agents</td><td class="value">059174K</td></tr>
    <tr><td class="label">Property Guild of Victoria Member</td><td class="value">Owners Corporation Chapter</td></tr>
    <tr><td class="label">Authorised Representative for:</td><td class="value">KSU<span class="sep">|</span><span class="url">www.ksu.com.au</span></td></tr>
    <tr><td class="label top" rowspan="3">Insurance distributor for:</td><td class="value">BTR<span class="sep">|</span><span class="url">www.btr.com.au</span></td></tr>
    <tr><td class="value tall">Tenement Cover Underwriters<span class="url-line">www.tcu.com.au</span></td></tr>
    <tr><td class="value tall">Common Property Assurance<span class="url-line">www.commonpropertyassure.com.au</span></td></tr>
  </table>

  <section class="indemnity">
    <h2>Professional Indemnity Insurance</h2>
    <p>Marrowfen Estate Agents carry $2 million Professional Indemnity insurance in excess of the prescribed amount under Section 119(5) of the Owners Corporation Act.</p>
  </section>

  <div class="garden-photo" role="img" aria-label="Landscaped communal garden with a gazebo, picnic table, palms, shrubs and trees under a clear sky"></div>
</main>
</body>
</html>
```